Upscale business cards needed for Board of Directors

We need professional business cards created for members of our family business Board of Directors. We would like these relatively simple and straightforward, but also with a unique element to set them apart. Probably stick with neutral and simple colors - white, grey etc. We need space for the traditional elements, including name, title, address, email/phone number. And we will be creating several from this template so it needs to be template that is easy to switch information in and out of.
Business
See description

```html
<!DOCTYPE html>
<html lang="en">
<head>
<meta charset="utf-8">
<title>Harbourline Holdings – Business Card</title>
<link href="https://fonts.googleapis.com/css2?family=Open+Sans:wght@400;600;700;800&display=swap" rel="stylesheet">
<style>
  :root {
    --backdrop: #cccccc;
    --card-gold: #b39b71;
    --card-black: #231f20;
    --ink: #1c1a1a;
    --logo-light: #e8e8e8;
  }
  html, body {
    margin: 0;
    padding: 0;
    width: 1200px;
    height: 900px;
    overflow: hidden;
    background: var(--backdrop);
    font-family: "Open Sans", Arial, sans-serif;
  }
  .canvas {
    position: relative;
    width: 1200px;
    height: 900px;
  }
  .card {
    position: absolute;
    top: 275px;
    width: 477px;
    height: 294px;
    box-sizing: border-box;
  }
  .card--front {
    left: 116px;
    background: var(--card-gold);
    border-radius: 0 56px 0 56px;
    color: var(--ink);
  }
  .card--back {
    left: 622px;
    background: var(--card-black);
    border-radius: 56px 0 56px 0;
  }
  .brand-name {
    position: absolute;
    margin: 0;
    font-weight: 800;
    text-transform: uppercase;
    line-height: 1.05;
    text-align: center;
  }
  .card--front .brand-name {
    left: 42px;
    top: 78px;
    width: 212px;
    font-size: 23px;
    letter-spacing: 1px;
    color: var(--ink);
  }
  .card--back .brand-name {
    left: 0;
    right: 0;
    top: 116px;
    font-size: 34px;
    letter-spacing: 2px;
    color: var(--logo-light);
  }
  .holder {
    position: absolute;
    right: 20px;
    top: 34px;
    text-align: right;
  }
  .holder__name {
    margin: 0;
    font-size: 19px;
    font-weight: 700;
    line-height: 1.1;
  }
  .holder__title {
    margin: 2px 0 0;
    font-size: 12.5px;
    line-height: 1.2;
  }
  .address {
    position: absolute;
    right: 21px;
    top: 156px;
    margin: 0;
    font-style: normal;
    font-size: 12.5px;
    line-height: 17px;
    text-align: right;
  }
  .contact-list {
    position: absolute;
    right: 19px;
    top: 217px;
    margin: 0;
    padding: 0;
    list-style: none;
    font-size: 12.5px;
    line-height: 17.5px;
  }
  .contact-list li {
    display: flex;
    justify-content: flex-end;
    align-items: center;
    gap: 7px;
  }
  .contact-list svg {
    width: 10px;
    height: 10px;
    fill: var(--ink);
  }
</style>
</head>
<body>
<div class="canvas">

  <section class="card card--front">
    <p class="brand-name">Harbourline<br>Holdings</p>

    <div class="holder">
      <h1 class="holder__name">Daniel Hart</h1>
      <p class="holder__title">Managing Director</p>
    </div>

    <address class="address">
      12345, Address Goes Here<br>
      Country Name, 123456
    </address>

    <ul class="contact-list">
      <li>044-123 456 789
        <svg viewBox="0 0 24 24" aria-hidden="true"><path d="M6.6 10.8a15.1 15.1 0 0 0 6.6 6.6l2.2-2.2a1 1 0 0 1 1-.25 11.4 11.4 0 0 0 3.6.57 1 1 0 0 1 1 1V20a1 1 0 0 1-1 1A17 17 0 0 1 3 4a1 1 0 0 1 1-1h3.5a1 1 0 0 1 1 1c0 1.25.2 2.45.57 3.57a1 1 0 0 1-.25 1z"/></svg>
      </li>
      <li>info@webname.com
        <svg viewBox="0 0 24 24" aria-hidden="true"><path d="M2 5h20v14H2z M3 6.5l9 6 9-6" stroke="#b39b71" stroke-width="1.6"/></svg>
      </li>
      <li>www.websitename.com
        <svg viewBox="0 0 24 24" aria-hidden="true"><path d="M10.6 13.4a1 1 0 0 1 0-1.4l3-3a1 1 0 1 1 1.4 1.4l-3 3a1 1 0 0 1-1.4 0zM8 21a5 5 0 0 1-3.5-8.5l2.3-2.3 1.4 1.4-2.3 2.3a3 3 0 0 0 4.2 4.2l2.3-2.3 1.4 1.4-2.3 2.3A5 5 0 0 1 8 21zm9.2-7.2-1.4-1.4 2.3-2.3a3 3 0 0 0-4.2-4.2l-2.3 2.3-1.4-1.4 2.3-2.3a5 5 0 0 1 7 7z"/></svg>
      </li>
    </ul>
  </section>

  <section class="card card--back">
    <p class="brand-name">Harbourline<br>Holdings</p>
  </section>

</div>
</body>
</html>
```